Dietitian/Nutritionist seeks trifold marketing brochure

We need a trifold brochure for marketing to patients within a doctors surgery. This will be a source of information for prospective patients, what they can expect and how to contact us. The brochure needs to have some key information such as a brief description of the services available, fees, locations of clinics and contact information. Our current brochure has been uploaded which has the information you need to complete this project. The files you provide will allow us to edit the information at a later date as pricing and services change.

Target Market(s)

Patients who have been referred to see a dietitian/nutritionist and people who are considering seeing a dietitian/nutritionist but haven't decided

Industry/Entity Type

Dietician

Font styles to use
Serif

Colors

Designer to choose colors to be used in the design.

Requirements
Must have
• My logo
• Accredited practising dietitian logo
• My website address and contact details
• Most of the information that is in my current brochure
• Locations/names of the four clinics
Nice to have
• Images that promote cooking, health and wellbeing

```html
<!DOCTYPE html>
<html lang="en">
<head>
<meta charset="utf-8">
<title>Riverside Nutrition & Dietetics – Trifold Brochure</title>
<link href="https://fonts.googleapis.com/css2?family=Cinzel:wght@400;600;700&family=Raleway:wght@400;500&display=swap" rel="stylesheet">
<style>
  :root{
    --navy:#1b3a96;
    --navy-deep:#15307f;
    --teal:#1d86b8;
    --green:#6cb52d;
    --green-light:#a6d63a;
    --ink:#444a55;
    --backdrop:#d8d8d8;
    --paper:#f7f9fc;
    --water:#b9d3ea;
    --badge:#f07b2a;
  }
  *{margin:0;padding:0;box-sizing:border-box}
  html,body{width:924px;height:1200px;overflow:hidden;background:var(--backdrop)}
  .brochure{position:absolute;left:22px;top:261px;width:880px;height:678px;background:var(--paper);overflow:hidden;box-shadow:0 2px 6px rgba(0,0,0,.25)}
  .backdrop-art{position:absolute;inset:0}
  .fold{position:absolute;top:0;bottom:0;width:293px}
  .fold-1{left:0;background:linear-gradient(90deg,rgba(0,0,0,.04),rgba(0,0,0,0) 30%)}
  .fold-2{left:293px;background:linear-gradient(90deg,rgba(0,0,0,.06),rgba(255,255,255,0) 25%,rgba(0,0,0,0) 80%,rgba(0,0,0,.03))}
  .fold-3{left:587px;background:linear-gradient(90deg,rgba(0,0,0,.06),rgba(0,0,0,0) 25%)}
  .abs{position:absolute}
  .small{font-family:'Raleway',Arial,sans-serif;font-size:9px;color:var(--ink)}
  .intro{left:0;width:293px;top:200px;text-align:center;font-family:'Cinzel',Georgia,serif;font-size:12.5px;line-height:16px;color:var(--navy-deep);font-weight:600}
  .svc-head{left:45px;font-family:'Cinzel',Georgia,serif;font-size:12.5px;font-weight:600;color:var(--navy)}
  .svc-item{left:55px}
  .svc-item::before{content:"";position:absolute;left:-9px;top:4px;width:4px;height:4px;border-radius:50%;background:var(--green)}
  .svc-note{left:45px}
  .tagline{left:293px;width:294px;top:174px;text-align:center;font-family:'Cinzel',Georgia,serif;font-weight:700;font-size:12.5px;line-height:18px;color:var(--green)}
  .closing{left:293px;width:294px;top:574px;text-align:center;font-family:'Cinzel',Georgia,serif;font-size:13px;line-height:17px;color:#2a2f3a}
  .footer-bar{left:0;right:0;bottom:0;height:27px;background:var(--navy-deep)}
  .footer-text{bottom:0;height:27px;line-height:27px;text-align:center;color:#fff;font-family:'Cinzel',Georgia,serif}
  .footer-web{font-size:10.5px;width:293px}
  .footer-phone{left:293px;width:294px;font-size:17px}
  .brand{left:587px;width:293px;top:82px;text-align:center;font-family:'Cinzel',Georgia,serif;color:var(--navy)}
  .brand-name{font-size:23px;font-weight:600;line-height:26px}
  .brand-sub{font-size:11px;font-weight:600;line-height:14px}
  .brand-dot{left:719px;top:26px;width:44px;height:44px;border-radius:50%;background:var(--teal)}
  .name{left:587px;width:293px;text-align:center;font-family:'Cinzel',Georgia,serif;font-weight:600;font-size:30px;line-height:34px}
  .name-first{top:242px;color:var(--teal)}
  .name-last{top:277px;color:var(--navy-deep)}
  .phone-pill{left:626px;top:325px;width:213px;height:31px;border-radius:16px;background:var(--navy);color:#fff;text-align:center;font-family:'Cinzel',Georgia,serif;font-size:21px;line-height:31px}
  .contact{left:587px;width:293px;text-align:center;font-family:'Cinzel',Georgia,serif;font-size:9px;color:#1f2530}
  .accredit{left:597px;top:596px;width:256px;height:46px;border-radius:23px;background:rgba(61,160,214,.75);border:2px solid rgba(255,255,255,.7)}
  .accredit-text{left:22px;top:7px;color:#fff;font-family:'Raleway',Arial,sans-serif;font-size:13px;line-height:16px}
  .accredit-badge{right:20px;top:5px;width:32px;height:32px;border-radius:4px;background:var(--badge)}
</style>
</head>
<body>
<div class="brochure">
  <svg class="backdrop-art" width="880" height="678" viewBox="0 0 880 678">
    <defs>
      <linearGradient id="water" x1="0" y1="0" x2="0" y2="1">
        <stop offset="0" stop-color="#ffffff" stop-opacity="0"/>
        <stop offset=".45" stop-color="#eef4fb"/>
        <stop offset="1" stop-color="#a9c8e4"/>
      </linearGradient>
      <linearGradient id="top-grey" x1="0" y1="0" x2="0" y2="1">
        <stop offset="0" stop-color="#dcdde0"/>
        <stop offset="1" stop-color="#ffffff" stop-opacity="0"/>
      </linearGradient>
      <linearGradient id="greenband" x1="0" y1="0" x2="1" y2="0">
        <stop offset="0" stop-color="#b5dc55"/>
        <stop offset=".5" stop-color="#8cc83a"/>
        <stop offset="1" stop-color="#5fae28"/>
      </linearGradient>
      <radialGradient id="fruit" cx=".45" cy=".45" r=".6">
        <stop offset="0" stop-color="#f6b43a"/>
        <stop offset=".6" stop-color="#f08a2a"/>
        <stop offset="1" stop-color="#e9eef2"/>
      </radialGradient>
      <radialGradient id="berry" cx=".5" cy=".5" r=".6">
        <stop offset="0" stop-color="#d8303f"/>
        <stop offset=".7" stop-color="#e4576a"/>
        <stop offset="1" stop-color="#ffffff"/>
      </radialGradient>
      <linearGradient id="stones" x1="0" y1="0" x2="0" y2="1">
        <stop offset="0" stop-color="#8e9299"/>
        <stop offset="1" stop-color="#4e535b"/>
      </linearGradient>
    </defs>
    <rect width="880" height="678" fill="#f7f9fc"/>
    <rect y="300" width="880" height="378" fill="url(#water)"/>
    <rect width="880" height="150" fill="url(#top-grey)"/>
    <!-- blue swoosh tapering to a point -->
    <path d="M0 120 C100 80 200 52 310 42 C200 58 100 102 0 152 Z" fill="var(--navy)"/>
    <path d="M0 152 C100 102 200 58 310 42 C200 64 100 112 0 164 Z" fill="#ffffff"/>
    <!-- pale highlight above the green wave -->
    <path d="M190 40 C330 18 470 34 592 100 C684 150 780 176 880 110 L880 122 C780 190 684 166 592 114 C470 48 330 30 190 40 Z" fill="#d8e8f3"/>
    <!-- green wave tapering in from the left -->
    <path d="M190 42 C330 22 470 40 592 112 C684 164 780 192 880 124 L880 158 C790 230 686 214 590 156 C480 88 340 50 190 42 Z" fill="url(#greenband)"/>
    <!-- image areas -->
    <g role="img" aria-label="Photo of fresh raspberries with a mint leaf">
      <circle cx="149" cy="105" r="77" fill="#ffffff" stroke="var(--green)" stroke-width="4"/>
      <circle cx="149" cy="105" r="58" fill="url(#berry)"/>
    </g>
    <g role="img" aria-label="Photo of citrus fruit, kiwi and juice with a stethoscope">
      <circle cx="441" cy="418" r="117" fill="#ffffff" stroke="var(--green)" stroke-width="4"/>
      <circle cx="441" cy="418" r="108" fill="url(#fruit)"/>
    </g>
    <g role="img" aria-label="Photo of balanced stones standing in calm water">
      <ellipse cx="762" cy="508" rx="46" ry="74" fill="url(#stones)" opacity=".85"/>
      <ellipse cx="762" cy="582" rx="96" ry="8" fill="#9fbedb" opacity=".6"/>
    </g>
  </svg>

  <div class="fold fold-1"></div>
  <div class="fold fold-2"></div>
  <div class="fold fold-3"></div>

  <!-- Panel 1: services -->
  <div class="abs intro">An Accredited Practising<br>Dietitian can assist you with:</div>

  <div class="abs svc-head" style="top:248px">Diabetes</div>
  <div class="abs small svc-item" style="top:274px">Impaired Glucose Tolerance,</div>
  <div class="abs small svc-item" style="top:290px">Gestational Diabetes</div>
  <div class="abs small svc-item" style="top:306px">Type 1 &amp; 2 Diabetes,</div>

  <div class="abs svc-head" style="top:325px">Digestive Health</div>
  <div class="abs small svc-item" style="top:351px">Irritable Bowel Syndrome</div>
  <div class="abs small svc-item" style="top:367px">Coeliac Disease</div>
  <div class="abs small svc-item" style="top:385px">Diverticular Disease</div>

  <div class="abs svc-head" style="top:405px">Gastric Banding</div>
  <div class="abs small svc-note" style="top:431px">and other surgical methods of</div>
  <div class="abs small svc-note" style="top:447px">weight loss</div>

  <div class="abs svc-head" style="top:469px">Cardiovascular</div>
  <div class="abs small svc-item" style="top:491px">High cholesterol</div>
  <div class="abs small svc-item" style="top:508px">High Blood Pressure</div>
  <div class="abs small svc-item" style="top:526px">Risk Reduction</div>

  <div class="abs svc-head" style="top:547px">Weight Management</div>
  <div class="abs small svc-note" style="top:567px">loss/gain and support</div>

  <div class="abs svc-head" style="top:591px">General</div>
  <div class="abs small svc-note" style="top:613px">Healthy Eating &amp; Nutrition</div>

  <!-- Panel 2: approach -->
  <div class="abs tagline">Helping you to meet your<br>individual nutrition goals<br>with an emphasis on<br>practical skills, everyday<br>foods, and providing you</div>
  <div class="abs closing">We work together to<br>develop personalised eating<br>plans that take</div>

  <!-- Panel 3: cover -->
  <div class="abs brand-dot"></div>
  <div class="abs brand">
    <div class="brand-name">Riverside</div>
    <div class="brand-sub">Nutrition &amp; Dietetics</div>
  </div>
  <div class="abs name name-first">Daniel</div>
  <div class="abs name name-last">Whitcombe</div>
  <div class="abs phone-pill">0400 555 218</div>
  <div class="abs contact" style="top:369px">DANIEL.W.NUTRITION@EXAMPLE.COM</div>
  <div class="abs contact" style="top:387px">FAX: 6300 4417</div>
  <div class="abs accredit">
    <div class="abs accredit-text">Accredited Practising<br>Dietitian &amp; Chef</div>
    <div class="abs accredit-badge"></div>
  </div>

  <!-- Footer -->
  <div class="abs footer-bar"></div>
  <div class="abs footer-text footer-web" style="left:0">WWW.RIVERSIDEDIETITIAN.COM.AU</div>
  <div class="abs footer-text footer-phone">0400 555 218</div>
  <div class="abs footer-text footer-web" style="left:587px">WWW.RIVERSIDEDIETITIAN.COM.AU</div>
</div>
</body>
</html>
```